K & R Acre Works. Business card design

We need a business card designed for a new business. We have a bulldozer and tractor service. We clear land and make wildlife food plots. We provide disking, bush hogging, and site prep services.
I have attached an image of a business card that I like and would like my business cards to look similar.

Target Market(s)

anyone needing bulldozer and/or tractor services

Industry/Entity Type

Business

Contact Information for Business Card

K & R Acre Works, Operated by 7-T-Ranch
Wade Colton
601-472-3358
wcr4817@fieldmail-example.com

Font styles to use
Sans Serif

Colors

Designer to choose colors to be used in the design.

Requirements
Must have
• image of tractor and bulldozer
• Land Clearing
• Wildlife food plots
• Bush Hogging
• Disking
• Site prep
Nice to have
• i have included a image of a business card that i like. I would like mine to be similar.

```html
<!DOCTYPE html>
<html lang="en">
<head>
<meta charset="utf-8">
<title>K &amp; R Acre Works – Business Card</title>
<link href="https://fonts.googleapis.com/css2?family=Roboto:wght@400;500;700&family=Roboto+Condensed:wght@700&display=swap" rel="stylesheet">
<style>
  :root {
    --page-bg: #3a3a3a;
    --olive: #9a9433;
    --brown: #6e4418;
    --orange: #b86e22;
    --card-white: #f3f3f3;
    --ink-light: #ffffff;
    --ink-dark: #2b2b2b;
    --logo-brown: #7a4a1c;
    --photo-dirt: #9c8d6a;
    --photo-green: #6f7a3e;
  }
  html, body {
    margin: 0;
    padding: 0;
    width: 1200px;
    height: 960px;
    overflow: hidden;
    background: var(--page-bg);
    font-family: "Roboto", Arial, sans-serif;
  }
  .business-card {
    position: absolute;
    left: 300px;
    top: 310px;
    width: 600px;
    height: 341px;
    border-radius: 18px;
    overflow: hidden;
    background: var(--card-white);
    box-shadow: 0 6px 14px rgba(0,0,0,0.45);
  }
  .card-shapes {
    position: absolute;
    inset: 0;
  }
  .contact-side {
    position: absolute;
    left: 27px;
    top: 56px;
    width: 205px;
    color: var(--ink-light);
  }
  .holder-name {
    margin: 0;
    font-family: "Roboto Condensed", "Roboto", sans-serif;
    font-weight: 700;
    font-size: 21px;
    line-height: 24px;
  }
  .holder-role {
    margin: 0;
    font-size: 14px;
    font-weight: 500;
    line-height: 18px;
  }
  .contact-list {
    margin: 20px 0 0;
    font-size: 13px;
    line-height: 18px;
  }
  .contact-list p {
    margin: 0;
    white-space: nowrap;
  }
  .contact-email {
    letter-spacing: -0.25px;
  }
  .services-heading {
    margin: 10px 0 0;
    font-family: "Roboto Condensed", "Roboto", sans-serif;
    font-weight: 700;
    font-size: 17px;
    line-height: 20px;
  }
  .services-list {
    margin: 0;
    padding: 0;
    list-style: none;
    font-size: 14px;
    line-height: 18px;
  }
  .services-list li::before {
    content: "•";
    margin-right: 6px;
  }
  .brand-block {
    position: absolute;
    left: 318px;
    top: 116px;
    width: 230px;
  }
  .brand-name {
    margin: 0;
    display: flex;
    align-items: center;
    gap: 6px;
    font-family: "Roboto", sans-serif;
    font-weight: 700;
    font-size: 19px;
    line-height: 22px;
    letter-spacing: 0.6px;
    color: var(--logo-brown);
    white-space: nowrap;
  }
  .brand-mark {
    width: 14px;
    height: 14px;
    background: var(--olive);
  }
  .brand-tagline {
    margin: 1px 0 0;
    font-size: 9.4px;
    font-weight: 500;
    color: var(--ink-dark);
    letter-spacing: 0.1px;
    white-space: nowrap;
  }
  .equipment-photos {
    display: flex;
    gap: 6px;
    margin-top: 8px;
  }
  .equipment-photo {
    height: 74px;
  }
  .photo-bulldozer {
    width: 124px;
    background: linear-gradient(180deg, #a7b49a 0%, var(--photo-dirt) 55%, #7d6f52 100%);
  }
  .photo-tractor {
    width: 100px;
    background: linear-gradient(180deg, #5e6b3a 0%, var(--photo-green) 50%, #a0885a 100%);
  }
</style>
</head>
<body>
  <div class="business-card">
    <svg class="card-shapes" width="600" height="341" viewBox="0 0 600 341" aria-hidden="true">
      <path d="M0 0 H340 C255 70 232 250 333 341 H0 Z" fill="var(--orange)"/>
      <path d="M0 0 H332 C248 72 228 245 326 341 H0 Z" fill="var(--card-white)"/>
      <path d="M0 0 H326 C242 74 226 240 322 341 H0 Z" fill="var(--brown)"/>
      <path d="M0 0 H318 C238 78 226 240 314 341 H0 Z" fill="var(--orange)"/>
      <path d="M0 0 H316 C236 80 224 240 311 341 H0 Z" fill="var(--ink-light)"/>
      <path d="M0 0 H313 C233 82 221 240 308 341 H0 Z" fill="var(--olive)"/>
    </svg>

    <div class="contact-side">
      <h1 class="holder-name">WADE COLTON</h1>
      <p class="holder-role">OWNER</p>
      <div class="contact-list">
        <p>(P) 601-472-3358</p>
        <p class="contact-email">(E) wcr4817@fieldmail-example.com</p>
        <p>www.kracreworks-example.com</p>
      </div>
      <h2 class="services-heading">WE CREADED</h2>
      <ul class="services-list">
        <li>Land Clearing</li>
        <li>Wildlife food plots</li>
        <li>Bush Hogging</li>
        <li>Disking • Site prep</li>
      </ul>
    </div>

    <div class="brand-block">
      <p class="brand-name"><span class="brand-mark"></span>K &amp; R ACRE WORKS</p>
      <p class="brand-tagline">FOR ALL OF YOUR LAND IMPROVEMENT NEEDS</p>
      <div class="equipment-photos">
        <div class="equipment-photo photo-bulldozer" role="img" aria-label="Photo of a yellow bulldozer pushing dirt on a cleared site"></div>
        <div class="equipment-photo photo-tractor" role="img" aria-label="Photo of an orange tractor with a front loader in a grassy field"></div>
      </div>
    </div>
  </div>
</body>
</html>
```